Advertising company unique advertising platform

we need a logo design for a new company based in Australia Melbourne. We develop innovated advertising platform where consumer can use this platform to get regular discount, as business owner they can use this platform for free advertisement. Payment for this advertisement platform only payable every two weeks, when I generate revenue for their business

Industry/Entity Type

Advertising

Contact Information for Business Card

Dale Morven | Co-Founder |Managing Director
Suite 718 240 Wattlebrook Lane Melbourne Vic 3000

ABN 38 614 207 923
Tel: +61 0487 259 318 | Email: dale.morven@plivorantu.com

Font styles to use
Decorative
Script

Requirements
Must have
• Try few different design and some round corner business card
Should not have
• One round corner business card...try 4 different colour background not only black, make sure two side is designed. Be creative so imagine you are giving this to a client make sure has wow factor, if you can also try one design with engrave like all the logo, words look 3d feel
• The word Advertising Platform use attached file font

```html
<!DOCTYPE html>
<html lang="en">
<head>
<meta charset="utf-8">
<title>Kelvane Hub – Business Card</title>
<link href="https://fonts.googleapis.com/css2?family=Roboto:wght@400;500;700&display=swap" rel="stylesheet">
<style>
  :root {
    --stage: #3b3b3b;
    --card: #1e1e1e;
    --card-front: #262626;
    --ember: #e9512b;
    --mint: #1fd8a8;
    --ink: #f1f1f1;
    --rule: #d9d9d9;
    --ghost: rgba(233, 120, 60, 0.16);
  }
  * { margin: 0; padding: 0; box-sizing: border-box; }
  html, body {
    width: 1200px; height: 886px; overflow: hidden;
    background: var(--stage);
    font-family: "Roboto", Arial, sans-serif;
  }
  .sheet {
    width: 1200px; height: 886px;
    display: flex; align-items: center; justify-content: center; gap: 40px;
  }
  .card {
    width: 560px; height: 320px; position: relative; overflow: hidden;
    box-shadow: 0 12px 30px rgba(0,0,0,0.45);
  }
  /* Back side */
  .card--back { background: var(--card); border-radius: 22px; }
  .back__mark {
    position: absolute; left: 50px; top: 60px;
    width: 200px; height: 200px; border-radius: 50%;
    background: var(--ghost);
  }
  .back__brand {
    position: absolute; right: 48px; top: 118px; text-align: right;
  }
  .back__name {
    font-weight: 700; font-size: 46px; letter-spacing: 1px;
    color: var(--mint); line-height: 1;
  }
  .back__web {
    margin-top: 14px; font-size: 13px; letter-spacing: 3px; color: var(--ink);
  }
  /* Front side */
  .card--front { background: var(--card-front); }
  .front__brand {
    position: absolute; top: 34px; left: 0; right: 0;
    display: flex; align-items: center; justify-content: center; gap: 10px;
  }
  .front__dot { width: 26px; height: 26px; border-radius: 50%; background: var(--ember); }
  .front__brand-name { font-weight: 700; font-size: 22px; color: var(--mint); letter-spacing: 0.5px; }
  .front__person { position: absolute; top: 96px; left: 0; right: 0; text-align: center; }
  .front__name { font-weight: 500; font-size: 22px; color: var(--ember); text-transform: uppercase; }
  .front__role { font-weight: 500; font-size: 15px; color: var(--mint); text-transform: uppercase; line-height: 1.3; margin-top: 4px; }
  .front__rule {
    position: absolute; top: 192px; left: 36px; right: 36px;
    height: 1px; background: var(--rule);
  }
  .front__contact {
    position: absolute; top: 210px; left: 0; right: 0; text-align: center;
    color: var(--ink); font-size: 14px; line-height: 1.6;
  }
  .contact__row { display: flex; justify-content: center; align-items: center; gap: 6px; }
  .contact__row svg { width: 12px; height: 12px; fill: var(--ember); }
  .contact__gap { width: 12px; }
</style>
</head>
<body>
<main class="sheet">
  <section class="card card--back" aria-label="Card back">
    <div class="back__mark"></div>
    <div class="back__brand">
      <div class="back__name">Kelvane Hub</div>
      <div class="back__web">www.plivorantu.com</div>
    </div>
  </section>

  <section class="card card--front" aria-label="Card front">
    <div class="front__brand">
      <span class="front__dot"></span>
      <span class="front__brand-name">Kelvane Hub</span>
    </div>
    <div class="front__person">
      <div class="front__name">Dale Morven</div>
      <div class="front__role">Co-Founder<br>Managing Director</div>
    </div>
    <div class="front__rule"></div>
    <div class="front__contact">
      <div class="contact__row">
        <svg viewBox="0 0 24 24" aria-hidden="true"><path d="M6.6 10.8a15.1 15.1 0 0 0 6.6 6.6l2.2-2.2a1 1 0 0 1 1-.25 11.4 11.4 0 0 0 3.6.57 1 1 0 0 1 1 1V20a1 1 0 0 1-1 1A17 17 0 0 1 3 4a1 1 0 0 1 1-1h3.5a1 1 0 0 1 1 1c0 1.25.2 2.45.57 3.57a1 1 0 0 1-.25 1z"/></svg>
        <span>+61 0487 259 318</span>
        <span class="contact__gap"></span>
        <svg viewBox="0 0 24 24" aria-hidden="true"><path d="M2 5h20v14H2z M2 5l10 8 10-8" /></svg>
        <span>dale.morven@plivorantu.com</span>
      </div>
      <div>Suite 718 240 Wattlebrook Lane, Melbourne Vic 3000</div>
      <div>Plivorantu, ABN 38 614 207 923</div>
    </div>
  </section>
</main>
</body>
</html>
```